Im want a website LIKE VRX's and FleetHollow.com's with product payment options like Trenzo's

I need a website LIKE VRX with a header made EXACTLY LIKE THAT OF FLEETHOLLOWS .

The front page photo should be like that of FLEETHOLLOW's webpage as well.

The name of the website will be called "M.K. (Caldera Key)".

We will be targeting ALL MARKETS in a small town in central Panama and charging businesses "listing fees" like a phone book does but also providing informational blogs, news, and other interesting activities.

THIS IS A MULTI PAGE WEBSITE

THIS IS WHERE VRX's website meets Brivelle/FleetHollow.

Once the layout is built I will tweak and modify, add information, and upload items for sale.

Here is a list of specific categories that should be listed out above the front page header image/search bar

-- Home -- News -- Travel -- Activities -- Shop & Dine -- Store -- More... --

These categories should be spread across the bottom of the page in three sections:

WHATS SO GREAT ABOUT (Caldera Key),
HAND PICKED TOURS
ACTIVITIES etc.

Also lets use www.Trenzo.example 's
"HOT DESTINATIONS"
"BEAT THE BEST PRICES IN BOQUETE"
"OCTOBERS INSIDER PICKS"
"TOP DESTINATIONS"
and spread them in four sections side-by-side near the bottom of the page.

Overall I would like to see the finished product to be something LIKE VRX's and FleetHollows.

WE NEED ONLINE PAYMENT OPTIONS LIKE BRIVELLE'S WEBSITE HAS

This will be a desktop website but should be very mobile friendly as well.

-rodmund

P.S. Good luck!

If it isn't already too late to change the website name, the name of the website should be "Caldera Key". Added Friday, October 9, 2015

What do you guys think the budget should be to win this? Added Saturday, October 10, 2015

www.palmorra.example is the most amazing simple site. Whoever can make me a replica with my specifications will win immediately!!!! Added Sunday, October 18, 2015

OMG www.palmorra.example is the bomb!So simple and elegant. Whoever can make me an EXACT REPLICA OF WWW.PALMORRA.EXAMPLE as my site with the specifications mentioned in my brief will take home the $825.00 immediately! Good luck amigos! Added Sunday, October 18, 2015

Does anybody know how to add recurring monthly billing options on this website? Added Sunday, October 18, 2015

ALL MARKETS

Product

Coded - Design and coding required

5+ page

• Coinvey payment options.
• I must be able to add and remove photos/text and video from the HTML files in the page.
• Be creative my friends, and may the odds be forever in your favor!
• I added some photos of a good layout for our page below.

```html
<!DOCTYPE html>
<html lang="en">
<head>
<meta charset="utf-8">
<title>Caldera Key</title>
<link href="https://fonts.googleapis.com/css2?family=Roboto:wght@400;500;700&family=Oswald:wght@500&display=swap" rel="stylesheet">
<style>
:root{
  --blue:#1c8fd9;
  --blue-dark:#0f5e96;
  --pink:#e8175d;
  --orange:#f7931e;
  --star:#f5a623;
  --ink:#333;
  --muted:#777;
  --cream:#fdf6dc;
  --footer:#2a2a2a;
  --footer-deep:#1e1e1e;
  --line:#e3e3e3;
}
*{box-sizing:border-box;margin:0;padding:0}
html,body{width:1200px;height:3688px;overflow:hidden}
body{font-family:"Roboto",Arial,sans-serif;color:var(--ink);background:#fff;font-size:12px;position:relative}
a{color:inherit;text-decoration:none}

/* hero */
.hero{position:absolute;top:0;left:0;width:1200px;height:580px}
.hero-photo{position:absolute;inset:0;background:linear-gradient(180deg,#4aa7e3 0%,#8cc8ee 35%,#c7a77e 70%,#8b6a4b 100%)}
.topbar{position:absolute;top:0;left:0;right:0;height:30px;background:rgba(10,50,90,.75);color:#fff;font-size:11px;display:flex;align-items:center;padding:0 60px;gap:14px}
.header{position:absolute;top:30px;left:0;right:0;height:64px;display:flex;align-items:center;justify-content:space-between;padding:0 60px;background:rgba(20,110,180,.55)}
.logo{font-family:"Oswald",sans-serif;font-size:30px;color:#fff;font-weight:500}
.nav{display:flex;gap:22px;font-size:11px;font-weight:700;color:#fff;text-transform:uppercase}
.search-panel{position:absolute;left:130px;top:262px;width:430px;height:108px;background:rgba(247,147,30,.92);padding:14px 20px;text-align:center}
.search-panel h2{color:#fff;font-size:22px;font-weight:700;letter-spacing:.5px;margin-bottom:14px}
.search-row{display:flex}
.search-row .field{flex:1;height:36px;background:#fff;color:#999;font-size:11px;padding:11px 10px;text-align:left}
.search-row .go{width:92px;height:36px;background:var(--pink);color:#fff;font-weight:700;font-size:12px;line-height:36px}
.dots{position:absolute;bottom:22px;left:0;right:0;display:flex;justify-content:center;gap:8px}
.dots span{width:10px;height:10px;border-radius:50%;background:rgba(255,255,255,.6)}
.dots span:first-child{background:#fff}

/* features strip */
.features{position:absolute;top:592px;left:0;width:1200px;height:120px;background:#fdf3d3;display:flex;align-items:center;padding:0 60px}
.features-tag{width:200px;height:88px;background:var(--pink);color:#fff;font-weight:700;font-size:17px;line-height:22px;display:flex;align-items:center;justify-content:center;text-align:center;padding:0 20px;margin-right:30px}
.feature{flex:1;text-align:center}
.feature svg{display:block;margin:0 auto 8px}
.feature b{display:block;color:var(--pink);font-size:13px}
.feature small{font-size:11px;color:var(--muted)}

/* sections */
.section{position:absolute;left:0;width:1200px}
.section-title{text-align:center;font-size:24px;font-weight:700;color:#444;letter-spacing:.5px;padding-top:30px}
.section-title::after{content:"";display:block;width:60px;height:3px;background:var(--pink);margin:10px auto 0}
.grid{display:grid;grid-template-columns:repeat(4,252px);gap:24px;width:1080px;margin:30px auto 0}

/* package card */
.card{height:360px;background:#fff}
.card .photo{height:180px}
.card h3{color:var(--blue);font-size:18px;font-weight:500;margin:14px 0 4px}
.stars{color:var(--star);font-size:13px;letter-spacing:1px}
.stars em{font-style:normal;color:var(--ink);font-size:11px;font-weight:700;margin-left:6px;letter-spacing:0}
.card p{font-size:11px;color:var(--muted);line-height:16px;margin:6px 0 10px}
.price-row{display:flex;align-items:flex-end;justify-content:space-between;border-top:1px solid var(--line);padding-top:8px}
.price-row small{display:block;font-size:9px;color:var(--muted);font-weight:700}
.price-row strong{font-size:22px;font-weight:700;color:#222}
.btn{background:var(--pink);color:#fff;font-size:10px;font-weight:700;padding:9px 14px}

/* listing */
.listing{background:var(--cream)}
.tabs{display:flex;justify-content:center;gap:6px;margin-top:22px}
.tabs span{font-size:10px;font-weight:700;padding:7px 16px;color:#555;background:#fff;border:1px solid var(--line)}
.tabs span.active{background:var(--orange);color:#fff;border-color:var(--orange)}
.lcard{height:310px}
.lcard .photo{height:120px}
.lcard h3{color:var(--blue);font-size:16px;font-weight:500;margin:12px 0 4px}
.lcard p{font-size:11px;color:var(--muted);line-height:16px;margin:8px 0}
.lcard a{color:var(--pink);font-size:11px;font-weight:700}

/* destinations */
.dest{display:grid;grid-template-columns:340px 360px 340px;gap:20px;width:1080px;margin:0 auto;padding-top:34px}
.dest h4{font-size:15px;font-weight:700;color:var(--blue);margin-bottom:14px;display:flex;align-items:center;gap:8px}
.dest h4.pink{color:var(--pink)}
.city-list{columns:2;list-style:none;font-size:11px;font-weight:700;color:#555;line-height:26px}
.crowds{display:flex;gap:12px}
.crowds .photo{width:130px;height:120px;flex:none;margin-top:8px}
.crowds p,.insider p{font-size:11px;color:var(--muted);line-height:17px}
.crowds ul{list-style:none;font-size:10px;font-weight:700;color:#555;line-height:20px;margin-top:6px}

/* newsletter */
.newsletter{background:var(--blue);display:flex;justify-content:space-between;align-items:center;padding:0 60px}
.nl-block{display:flex;align-items:center;gap:14px}
.nl-block h4{color:#fff;font-size:16px;font-weight:700;width:260px;display:flex;gap:8px;align-items:center}
.nl-block .field{width:220px;height:34px;background:#fff;color:#999;font-size:11px;padding:10px}
.nl-block .go{background:var(--orange);color:#fff;font-weight:700;font-size:11px;height:34px;line-height:34px;padding:0 18px}

/* footer */
.footer{background:var(--footer);color:#bbb;display:grid;grid-template-columns:280px 150px 150px 170px 1fr;gap:30px;padding:40px 60px 0}
.footer .logo{font-size:24px;margin-bottom:12px}
.footer p{font-size:11px;line-height:17px}
.footer h5{color:#fff;font-size:13px;font-weight:700;margin-bottom:12px}
.footer ul{list-style:none;font-size:11px;line-height:21px}
.mileage{display:flex;align-items:center;gap:10px;margin-bottom:24px}
.mileage i{width:46px;height:46px;border-radius:50%;background:var(--orange);display:block}
.mileage span{background:var(--footer-deep);color:#fff;font-weight:700;font-size:12px;padding:10px 14px}
.apps{display:flex;gap:8px;margin-top:8px}
.apps i{width:22px;height:22px;background:#555;display:block;border-radius:4px}
.social{display:flex;gap:6px;position:absolute;right:60px;bottom:18px}
.social i{width:22px;height:22px;border-radius:50%;background:var(--blue);display:block}
.bottombar{background:var(--footer-deep);color:#888;font-size:10px;display:flex;align-items:center;padding:0 60px}
</style>
</head>
<body>

<section class="hero">
  <div class="hero-photo" role="img" aria-label="Travel photo: couple smiling in front of an ancient amphitheatre under a blue sky"></div>
  <div class="topbar"><a href="#">Login / Register</a><span>|</span><a href="#">My Cart</a><span>|</span><a href="#">Help</a></div>
  <header class="header">
    <div class="logo">Caldera Key</div>
    <nav class="nav"><a href="#">Home</a><a href="#">About</a><a href="#">Guided Tours</a><a href="#">Hotel/Hostels</a><a href="#">Rental Vehicles</a><a href="#">News &amp; Events</a><a href="#">Contact</a></nav>
  </header>
  <div class="search-panel">
    <h2>LET THE ACTIVITIES BEGIN!</h2>
    <div class="search-row"><div class="field">Search for adventures, tours, vehicles, hotels...</div><div class="go">LET'S GO</div></div>
  </div>
  <div class="dots"><span></span><span></span><span></span><span></span></div>
</section>

<section class="features">
  <div class="features-tag">What So Great About Caldera Key</div>
  <div class="feature"><svg width="34" height="34" viewBox="0 0 34 34"><circle cx="17" cy="17" r="16" fill="#f7931e"/><path d="M10 17l5 5 9-10" stroke="#fff" stroke-width="3" fill="none"/></svg><b>HANDPICKED</b><small>Tours &amp; Activity</small></div>
  <div class="feature"><svg width="34" height="34" viewBox="0 0 34 34"><circle cx="17" cy="17" r="16" fill="#1c8fd9"/><path d="M10 17l5 5 9-10" stroke="#fff" stroke-width="3" fill="none"/></svg><b>VERIFIED</b><small>Reviews &amp; Photos</small></div>
  <div class="feature"><svg width="34" height="34" viewBox="0 0 34 34"><circle cx="17" cy="17" r="16" fill="#e8175d"/><path d="M17 8l3 6 6 1-4.5 4 1 6-5.5-3-5.5 3 1-6L8 15l6-1z" fill="#fff"/></svg><b>VIP CORNER</b><small>Access</small></div>
  <div class="feature"><svg width="34" height="34" viewBox="0 0 34 34"><circle cx="17" cy="17" r="16" fill="#f7931e"/><text x="17" y="23" text-anchor="middle" font-size="16" font-weight="700" fill="#fff" font-family="Roboto,sans-serif">$</text></svg><b>LOW PRICES</b><small>Guaranteed</small></div>
  <div class="feature"><svg width="34" height="34" viewBox="0 0 34 34"><circle cx="17" cy="17" r="16" fill="#1c8fd9"/><path d="M12 10c-2 2-2 6 3 11s9 5 11 3l-3-4-3 2c-2-1-4-3-5-5l2-3z" fill="#fff"/></svg><b>24/7 SUPPORT</b><small>With Live Chat</small></div>
</section>

<section class="section" style="top:712px;height:888px">
  <h2 class="section-title">FEATURED PACKAGES</h2>
  <div class="grid">
    <article class="card"><div class="photo" role="img" aria-label="White and blue seaside village on a cliff" style="background:linear-gradient(160deg,#5aa9e6,#e9eef2)"></div><h3>Popular Sightseeing</h3><div class="stars">★★★★★<em>225 Reviews</em></div><p>Quisque aliquam nibh a dui iaculis viverra id a velit ultrices posuere.</p><div class="price-row"><div><small>START FROM</small><strong>$420.00</strong></div><a class="btn">VIEW DETAILS</a></div></article>
    <article class="card"><div class="photo" role="img" aria-label="Temple ruins on a sunny hillside" style="background:linear-gradient(160deg,#7fb5e0,#c9a77a)"></div><h3>Special Guided Tours</h3><div class="stars">★★★★★<em>225 Reviews</em></div><p>Quisque aliquam nibh a dui iaculis viverra id a velit ultrices posuere.</p><div class="price-row"><div><small>START FROM</small><strong>$420.00</strong></div><a class="btn">VIEW DETAILS</a></div></article>
    <article class="card"><div class="photo" role="img" aria-label="Historic hotel building with green trees" style="background:linear-gradient(160deg,#3b7bc4,#d9c27a 60%,#5c8f3a)"></div><h3>Hotel/Hostels</h3><div class="stars">★★★★★<em>225 Reviews</em></div><p>Quisque aliquam nibh a dui iaculis viverra id a velit ultrices posuere.</p><div class="price-row"><div><small>START FROM</small><strong>$420.00</strong></div><a class="btn">VIEW DETAILS</a></div></article>
    <article class="card"><div class="photo" role="img" aria-label="Row of rental scooters parked on a street" style="background:linear-gradient(160deg,#9aa3ab,#4f5a63)"></div><h3>Rental Vehicles</h3><div class="stars">★★★★★<em>225 Reviews</em></div><p>Quisque aliquam nibh a dui iaculis viverra id a velit ultrices posuere.</p><div class="price-row"><div><small>START FROM</small><strong>$420.00</strong></div><a class="btn">VIEW DETAILS</a></div></article>
    <article class="card"><div class="photo" role="img" aria-label="Canal city with boats and old buildings" style="background:linear-gradient(160deg,#8fc1e3,#b99a73)"></div><h3>Popular Sightseeing</h3><div class="stars">★★★★★<em>225 Reviews</em></div><p>Quisque aliquam nibh a dui iaculis viverra id a velit ultrices posuere.</p><div class="price-row"><div><small>START FROM</small><strong>$420.00</strong></div><a class="btn">VIEW DETAILS</a></div></article>
    <article class="card"><div class="photo" role="img" aria-label="Traveller taking a photo with a camera" style="background:linear-gradient(160deg,#6fa8d8,#c8b49a)"></div><h3>Special Guided Tours</h3><div class="stars">★★★★★<em>225 Reviews</em></div><p>Quisque aliquam nibh a dui iaculis viverra id a velit ultrices posuere.</p><div class="price-row"><div><small>START FROM</small><strong>$420.00</strong></div><a class="btn">VIEW DETAILS</a></div></article>
    <article class="card"><div class="photo" role="img" aria-label="Happy traveller on a sunny beach" style="background:linear-gradient(160deg,#ffd36b,#e9a64f)"></div><h3>Hotel/Hostels</h3><div class="stars">★★★★★<em>225 Reviews</em></div><p>Quisque aliquam nibh a dui iaculis viverra id a velit ultrices posuere.</p><div class="price-row"><div><small>START FROM</small><strong>$420.00</strong></div><a class="btn">VIEW DETAILS</a></div></article>
    <article class="card"><div class="photo" role="img" aria-label="Scenic coastline at sunset" style="background:linear-gradient(160deg,#4f8fc6,#8cb6d6)"></div><h3>Rental Vehicles</h3><div class="stars">★★★★★<em>225 Reviews</em></div><p>Quisque aliquam nibh a dui iaculis viverra id a velit ultrices posuere.</p><div class="price-row"><div><small>START FROM</small><strong>$420.00</strong></div><a class="btn">VIEW DETAILS</a></div></article>
  </div>
</section>

<section class="section listing" style="top:1600px;height:870px">
  <h2 class="section-title">FEATURED LISTING</h2>
  <div class="tabs"><span class="active">TOURS ALL</span><span>GUIDED TOURS</span><span>HOTEL/HOSTELS</span><span>RENTAL VEHICLES</span></div>
  <div class="grid" style="margin-top:28px">
    <article class="lcard"><div class="photo" role="img" aria-label="Cathedral tower against a blue sky" style="background:linear-gradient(160deg,#77b3e3,#b89c78)"></div><h3>Fusce accumsan</h3><div class="stars">★★★★☆</div><p>Quisque aliquam nibh a dui iaculis viverra id a velit ultrices posuere lorem. Donec tempus at sed finibus pretium.</p><a>Read More »</a></article>
    <article class="lcard"><div class="photo" role="img" aria-label="Harbour with moored sailing boats" style="background:linear-gradient(160deg,#5c9bd0,#3e6f95)"></div><h3>Fusce accumsan</h3><div class="stars">★★★★☆</div><p>Quisque aliquam nibh a dui iaculis viverra id a velit ultrices posuere lorem. Donec tempus at sed finibus pretium.</p><a>Read More »</a></article>
    <article class="lcard"><div class="photo" role="img" aria-label="Colourful market street with shops" style="background:linear-gradient(160deg,#d9a05b,#8b5a3c)"></div><h3>Fusce accumsan</h3><div class="stars">★★★★☆</div><p>Quisque aliquam nibh a dui iaculis viverra id a velit ultrices posuere lorem. Donec tempus at sed finibus pretium.</p><a>Read More »</a></article>
    <article class="lcard"><div class="photo" role="img" aria-label="Group of friends on a road trip" style="background:linear-gradient(160deg,#a3c6e6,#6a8aa6)"></div><h3>Fusce accumsan</h3><div class="stars">★★★★☆</div><p>Quisque aliquam nibh a dui iaculis viverra id a velit ultrices posuere lorem. Donec tempus at sed finibus pretium.</p><a>Read More »</a></article>
    <article class="lcard"><div class="photo" role="img" aria-label="Old town square with church domes" style="background:linear-gradient(160deg,#86bde6,#c6ad85)"></div><h3>Fusce accumsan</h3><div class="stars">★★★★☆</div><p>Quisque aliquam nibh a dui iaculis viverra id a velit ultrices posuere lorem. Donec tempus at sed finibus pretium.</p><a>Read More »</a></article>
    <article class="lcard"><div class="photo" role="img" aria-label="Crowd walking through a festival" style="background:linear-gradient(160deg,#c98b5a,#6d4b3a)"></div><h3>Fusce accumsan</h3><div class="stars">★★★★☆</div><p>Quisque aliquam nibh a dui iaculis viverra id a velit ultrices posuere lorem. Donec tempus at sed finibus pretium.</p><a>Read More »</a></article>
    <article class="lcard"><div class="photo" role="img" aria-label="Riverside buildings in warm evening light" style="background:linear-gradient(160deg,#e7b46a,#9b6a45)"></div><h3>Fusce accumsan</h3><div class="stars">★★★★☆</div><p>Quisque aliquam nibh a dui iaculis viverra id a velit ultrices posuere lorem. Donec tempus at sed finibus pretium.</p><a>Read More »</a></article>
    <article class="lcard"><div class="photo" role="img" aria-label="Mountain lake under a clear sky" style="background:linear-gradient(160deg,#4d8ed0,#2f6aa3)"></div><h3>Fusce accumsan</h3><div class="stars">★★★★☆</div><p>Quisque aliquam nibh a dui iaculis viverra id a velit ultrices posuere lorem. Donec tempus at sed finibus pretium.</p><a>Read More »</a></article>
  </div>
</section>

<section class="section" style="top:2470px;height:320px">
  <div class="dest">
    <div>
      <h4><svg width="12" height="16" viewBox="0 0 12 16"><path d="M6 0a6 6 0 0 0-6 6c0 4.5 6 10 6 10s6-5.5 6-10a6 6 0 0 0-6-6z" fill="#f7931e"/><circle cx="6" cy="6" r="2.2" fill="#fff"/></svg>HOT DESTINATIONS</h4>
      <ul class="city-list"><li>PARIS</li><li>LAS VEGAS</li><li>ROME</li><li>NEW YORK CITY</li><li>LONDON</li><li>AMSTERDAM</li><li>BARCELONA</li><li>FLORENCE</li><li>VENICE</li><li>MILAN</li><li>MADRID</li><li>TOKYO</li><li>SYDNEY</li><li>DUBLIN</li></ul>
    </div>
    <div>
      <h4><svg width="14" height="14" viewBox="0 0 14 14"><rect width="14" height="14" fill="#1c8fd9"/><path d="M3 7l3 3 5-6" stroke="#fff" stroke-width="2" fill="none"/></svg>BEAT THE CROWDS IN EUROPE</h4>
      <p>Skip the lines at top attractions and enjoy priority entry with our hand picked local guides all season long.</p>
      <div class="crowds">
        <div class="photo" role="img" aria-label="Famous landmark tower in a European city" style="background:linear-gradient(160deg,#7fb4e2,#c7a27a)"></div>
        <ul><li>ARTIC STAIRS</li><li>HIPPODROMESIDE</li><li>GRAND FORUM</li><li>OLD HARBOUR</li><li>ROYAL GARDENS</li></ul>
      </div>
    </div>
    <div class="insider">
      <h4 class="pink"><svg width="14" height="14" viewBox="0 0 14 14"><path d="M7 0l2 5h5l-4 3 1.5 5L7 10l-4.5 3L4 8 0 5h5z" fill="#e8175d"/></svg>OCTOBER INSIDER'S PICK</h4>
      <p>Sed ut perspiciatis unde omnis iste natus error sit voluptatem accusantium doloremque laudantium, totam rem aperiam eaque ipsa quae ab illo inventore veritatis et quasi architecto beatae vitae dicta sunt explicabo. Nemo enim ipsam voluptatem quia voluptas sit aspernatur aut odit aut fugit.</p>
    </div>
  </div>
</section>

<section class="section" style="top:2790px;height:470px">
  <h2 class="section-title">PAYMENT PROCESS</h2>
  <div class="grid">
    <article class="card"><div class="photo" role="img" aria-label="White and blue seaside village on a cliff" style="background:linear-gradient(160deg,#5aa9e6,#e9eef2)"></div><h3>Popular Sightseeing</h3><div class="stars">★★★★★<em>225 Reviews</em></div><p>Quisque aliquam nibh a dui iaculis viverra id a velit ultrices posuere.</p><div class="price-row"><div><small>START FROM</small><strong>$420.00</strong></div><a class="btn">VIEW DETAILS</a></div></article>
    <article class="card"><div class="photo" role="img" aria-label="Temple ruins on a sunny hillside" style="background:linear-gradient(160deg,#7fb5e0,#c9a77a)"></div><h3>Special Guided Tours</h3><div class="stars">★★★★★<em>225 Reviews</em></div><p>Quisque aliquam nibh a dui iaculis viverra id a velit ultrices posuere.</p><div class="price-row"><div><small>START FROM</small><strong>$420.00</strong></div><a class="btn">VIEW DETAILS</a></div></article>
    <article class="card"><div class="photo" role="img" aria-label="Historic hotel building with green trees" style="background:linear-gradient(160deg,#3b7bc4,#d9c27a 60%,#5c8f3a)"></div><h3>Hotel/Hostels</h3><div class="stars">★★★★★<em>225 Reviews</em></div><p>Quisque aliquam nibh a dui iaculis viverra id a velit ultrices posuere.</p><div class="price-row"><div><small>START FROM</small><strong>$420.00</strong></div><a class="btn">VIEW DETAILS</a></div></article>
    <article class="card"><div class="photo" role="img" aria-label="Row of rental scooters parked on a street" style="background:linear-gradient(160deg,#9aa3ab,#4f5a63)"></div><h3>Rental Vehicles</h3><div class="stars">★★★★★<em>225 Reviews</em></div><p>Quisque aliquam nibh a dui iaculis viverra id a velit ultrices posuere.</p><div class="price-row"><div><small>START FROM</small><strong>$420.00</strong></div><a class="btn">VIEW DETAILS</a></div></article>
  </div>
</section>

<section class="section newsletter" style="top:3260px;height:100px">
  <div class="nl-block"><h4><svg width="16" height="12" viewBox="0 0 16 12"><rect width="16" height="12" fill="#fff"/><path d="M0 0l8 6 8-6" stroke="#1c8fd9" fill="none"/></svg>NEWSLETTER SUBSCRIBE</h4><div class="field">Enter Email</div><div class="go">SUBSCRIBE</div></div>
  <div class="nl-block"><h4 style="width:230px"><svg width="14" height="14" viewBox="0 0 14 14"><circle cx="6" cy="6" r="4.5" stroke="#fff" stroke-width="2" fill="none"/><path d="M9.5 9.5L13 13" stroke="#fff" stroke-width="2"/></svg>FIND YOUR NEXT ACTIVITY</h4><div class="field">Enter Email</div><div class="go">SEARCH NOW</div></div>
</section>

<footer class="section footer" style="top:3360px;height:260px">
  <div><div class="logo">Caldera Key</div><p>Quisque aliquam nibh a dui iaculis viverra id a velit ultrices posuere. Donec tempus at sed finibus pretium, sed ultrices lectus. Nam vitae arcu at nisl mattis vulputate a vel dolor.</p></div>
  <div><h5>COMPANY</h5><ul><li>About Us</li><li>Guided Tours</li><li>Hotel/Hostels</li><li>Careers</li><li>Press Room</li></ul></div>
  <div><h5>SUPPORT</h5><ul><li>Customer Care</li><li>Privacy Policy</li><li>Terms of Use</li><li>Payment Options</li><li>Site Map</li></ul></div>
  <div><h5>PARTNERSHIP</h5><ul><li>List Your Business</li><li>Affiliate Program</li><li>Advertise With Us</li><li>Travel Agents</li></ul></div>
  <div><div class="mileage"><i></i><span>MILEAGE PROGRAM</span></div><h5>MOBILE APP</h5><div class="apps"><i></i><i></i><i></i></div></div>
  <div class="social"><i></i><i></i><i></i><i></i><i></i><i></i></div>
</footer>

<div class="section bottombar" style="top:3620px;height:68px">Copyright © 2015 Caldera Key. All rights reserved.</div>

</body>
</html>
```